Vellmore Family Law, legal technician needs a website and design

I need a website for a family law practice. I specialize in collaborative law, unbundled services, and mediation. The website must contain my company logo (file attached), and the website must be a mixture of my personality and my profession. I have attached additional information to explain my personality and profession.

Target Market(s)

Lower through middle-class (income level up to $200,000 per year)

Coding

Coded - Design and coding required

Number of Pages Required

1 page

Requirements
Must have
• Must have enough pages to cover required content. I submitted below some content about the collaborative law process. All of the content is not necessary. However, the website must have enough content to clearly describe the services I offer. Use your professionalism and judgment regarding font, font size, etc.

```html
<!DOCTYPE html>
<html lang="en">
<head>
<meta charset="utf-8">
<title>About Darnell | Vellmore Family Law</title>
<link href="https://fonts.googleapis.com/css2?family=Cinzel:wght@600;700&family=Open+Sans:wght@400;600&family=Ubuntu:wght@400;500&display=swap" rel="stylesheet">
<style>
:root{
  --gold:#a39434;
  --gold-dark:#7f7a12;
  --olive:#a7a43a;
  --olive-button:#b2ac3c;
  --ink:#14142a;
  --text:#2b2b2b;
  --dark:#191919;
  --bar:#3d3d3d;
  --white:#fff;
  --line:#9a9a9a;
}
*{margin:0;padding:0;box-sizing:border-box}
html,body{width:1200px;height:2702px;overflow:hidden}
body{position:relative;background:var(--white);font-family:"Open Sans",Arial,sans-serif;color:var(--text)}
.abs{position:absolute}

/* brand lockup */
.brand{display:flex;align-items:center;gap:12px}
.brand-mark{width:14px;height:14px;background:var(--gold);flex:none}
.brand-name{font-family:"Cinzel",serif;font-weight:600;color:var(--gold);white-space:nowrap}

/* header */
.site-header{left:0;top:0;width:1200px;height:98px;background:var(--white);box-shadow:0 2px 6px rgba(0,0,0,.15);z-index:2}
.header-brand{left:140px;top:36px}
.header-brand .brand-name{font-size:19px}
.main-nav{left:497px;top:43px;display:flex;gap:20px;font-family:"Ubuntu",sans-serif;font-weight:500;font-size:12px;color:#111;white-space:nowrap}
.socials{left:905px;top:37px;display:flex;gap:6px}
.socials span{width:27px;height:27px;border-radius:50%;background:var(--gold);display:block}

/* hero */
.hero{left:0;top:98px;width:1200px;height:314px;background:linear-gradient(180deg,#eeeaec 0%,#e6dde7 60%,#ddd3df 100%);overflow:hidden}
.hero-skyline{left:860px;top:0;width:340px;height:314px;background:linear-gradient(180deg,rgba(90,100,120,0) 0%,rgba(90,100,120,.2) 55%,rgba(70,80,100,.45) 100%)}
.hero-title{left:0;top:124px;width:1200px;text-align:center;font-family:"Cinzel",serif;font-weight:700;font-size:50px;line-height:60px;color:var(--ink);letter-spacing:1px}

/* about */
.portrait-frame{left:133px;top:508px;width:383px;height:565px;border-top:5px solid var(--gold-dark);border-left:5px solid var(--gold-dark)}
.portrait{left:139px;top:514px;width:382px;height:565px;background:linear-gradient(160deg,#5d8a3a 0%,#3f6f34 35%,#2d3e5c 60%,#8a5a3a 100%)}
.about-copy{left:549px;top:534px;width:512px}
.about-copy .square{width:16px;height:16px;background:var(--gold);margin-bottom:14px}
.about-copy h2{font-family:"Cinzel",serif;font-weight:700;font-size:27px;color:var(--ink);letter-spacing:.5px}
.about-copy .rule{width:92px;height:2px;background:var(--gold);margin:10px 0 30px}
.about-copy p{font-size:10px;line-height:18px;text-align:justify;margin-bottom:17px;color:#333}
.about-copy h3{font-family:"Ubuntu",sans-serif;font-weight:500;font-size:15px;color:#111;margin:23px 0 15px}

/* credentials */
.credentials{left:138px;top:1158px;width:923px;height:233px;border:1px solid var(--line)}
.cred-photo{left:145px;top:1164px;width:262px;height:220px;background:linear-gradient(180deg,#d9ddd8 0%,#b7a48d 45%,#3a3b48 100%)}
.cred-copy{left:434px;top:1180px;font-size:11px;color:#333}
.cred-copy h3{font-family:"Ubuntu",sans-serif;font-weight:400;font-size:17.5px;color:#111;margin-bottom:15px}
.cred-copy ul{list-style:none}
.cred-copy li{display:flex;align-items:center;gap:8px;height:21.5px}
.cred-copy li svg{width:9px;height:9px}
.cred-copy .plain{height:21.5px;line-height:21.5px}
.cred-copy .bar-title{margin-top:4px}

/* collaborative */
.collab-band{left:0;top:1440px;width:1200px;height:682px;background:linear-gradient(180deg,#fff 0%,#f3f1ec 40%,#e4e1d6 100%)}
.collab-title{left:0;top:1506px;width:1200px;text-align:center;font-family:"Cinzel",serif;font-weight:700;font-size:28px;color:var(--ink)}
.collab-lead{left:150px;top:1554px;width:900px;text-align:center;font-size:11px;line-height:22px;color:#222}
.collab-cta{left:365px;top:1613px;width:471px;height:47px;background:var(--olive-button);display:flex;align-items:center;justify-content:center;font-family:"Ubuntu",sans-serif;font-size:13px;color:#2a2a10}
.collab-cta b{font-weight:500;margin-right:6px}
.video{left:259px;top:1697px;width:683px;height:352px;border:2px solid #ddd;box-shadow:0 2px 6px rgba(0,0,0,.3);background:#4e6e72}
.video-scene{left:261px;top:1699px;width:679px;height:324px;background:linear-gradient(180deg,#6d8b8d 0%,#587578 60%,#4a5c5f 100%)}
.play{left:568px;top:1850px;width:64px;height:42px;border-radius:8px;background:#111}
.controls{left:261px;top:2023px;width:679px;height:26px;background:linear-gradient(#f5f5f5,#cfcfcf);display:flex;align-items:center;gap:8px;padding:0 8px;font-size:8px;color:#333}
.controls .track{flex:1;height:4px;border-radius:2px;background:#999}

/* footer */
.site-footer{left:0;top:2122px;width:1200px;height:518px;background:var(--dark);border-top:4px solid var(--olive)}
.footer-brand{left:140px;top:2306px;gap:14px}
.footer-brand .brand-mark{width:20px;height:20px}
.footer-brand .brand-name{font-size:26px}
.contact-line{left:136px;display:flex;gap:10px;color:var(--white)}
.contact-line .icon{width:40px;height:40px;border-radius:50%;background:var(--olive);display:flex;align-items:center;justify-content:center;flex:none}
.contact-line .label{font-family:"Ubuntu",sans-serif;font-weight:500;font-size:12px;margin-top:4px}
.contact-line .value{font-family:"Ubuntu",sans-serif;font-size:17px;margin-top:3px}
.contact-panel{left:503px;top:2198px;width:558px;height:407px;background:linear-gradient(135deg,#8f8836 0%,#9c9540 50%,#847e32 100%)}
.contact-panel h2{position:absolute;left:34px;top:53px;font-family:"Cinzel",serif;font-weight:700;font-size:27px;color:var(--white)}
.field{position:absolute;background:var(--white);font-size:12px;color:#555;padding:0 12px;display:flex;align-items:center}
.field.msg{align-items:flex-start;padding-top:16px}
.submit{position:absolute;left:35px;top:301px;width:102px;height:48px;background:var(--dark);color:var(--white);font-family:"Ubuntu",sans-serif;font-weight:500;font-size:14px;display:flex;align-items:center;justify-content:center}
.legal{left:0;top:2640px;width:1200px;height:62px;background:var(--bar);color:var(--white);font-size:11px;display:flex;align-items:center;justify-content:center}
</style>
</head>
<body>

<header class="site-header abs">
  <div class="brand header-brand abs"><span class="brand-mark"></span><span class="brand-name">Vellmore Family Law</span></div>
  <nav class="main-nav abs"><span>HOME</span><span>ABOUT US</span><span>BENEFITS</span><span>OUR FEATURES</span><span>CONTACT US</span></nav>
  <div class="socials abs" aria-label="Social links"><span></span><span></span><span></span><span></span><span></span></div>
</header>

<section class="hero abs" aria-label="Page banner">
  <div class="hero-skyline abs" role="img" aria-label="City skyline with observation tower at dusk"></div>
  <h1 class="hero-title abs">ABOUT DARNELL</h1>
</section>

<div class="portrait-frame abs"></div>
<div class="portrait abs" role="img" aria-label="Portrait of Darnell Okafor in a navy suit standing among greenery"></div>

<article class="about-copy abs">
  <div class="square"></div>
  <h2>ABOUT DARNELL</h2>
  <div class="rule"></div>
  <p>My name is Darnell Okafor, and I am the owner of Vellmore Family Law, Legal Technician in King County, Washington, where I practice exclusively in Superior Court. I am passionate about helping people resolve their family law disputes.</p>
  <h3>Journey to Practicing Law:</h3>
  <p>I became interested in family law after struggling personally with a child support modification. As I completed my own forms, there were many errors needing correction. Every law clerk I asked for assistance told me they could not give legal advice and consult an attorney. I could not afford an attorney, and at that time, there were few, if any, pro bono (free) services available to low-income persons like me. After years of trial and error, I finally got a judge to sign my orders.</p>
  <p style="margin-top:20px">While preparing my child support modification, I spoke to many African American men with children in similar situations (court-ordered child support based on imputed and speculative income standards). African-American men struggling through the legal system is the impetus for opening a collaborative law practice. Here we the parties create an agreement without going to trial by negotiating a just and equitable agreement where both parties are satisfied with the outcome and in the child's best interest.</p>
  <p>Today, I am honored to be the solo practitioner at Vellmore Family Law, Legal Technician. I coordinate with other professionals, including attorneys, financial consultants, guardian ad litem, and family therapists, to identify an equitable and just agreement for my clients. I aim to help families and individuals in need of legal assistance, and give them an alternative to the inherent costly traditional courtroom battles with a collaborative law approach to dispute resolution.</p>
</article>

<div class="credentials abs"></div>
<div class="cred-photo abs" role="img" aria-label="Head and shoulders portrait of Darnell Okafor smiling"></div>
<section class="cred-copy abs">
  <h3>Education &amp; Creditials:</h3>
  <ul>
    <li><svg viewBox="0 0 10 10"><path d="M1 5l3 3 5-7" fill="none" stroke="#8a8a1a" stroke-width="2"/></svg>LLLT, Cascadia State University, School of Law</li>
    <li><svg viewBox="0 0 10 10"><path d="M1 5l3 3 5-7" fill="none" stroke="#8a8a1a" stroke-width="2"/></svg>B.A. Information Technology Administration Management, Evergreen Valley University</li>
    <li><svg viewBox="0 0 10 10"><path d="M1 5l3 3 5-7" fill="none" stroke="#8a8a1a" stroke-width="2"/></svg>A.S. Paralegal Studies, Pinecrest Community College</li>
    <li><svg viewBox="0 0 10 10"><path d="M1 5l3 3 5-7" fill="none" stroke="#8a8a1a" stroke-width="2"/></svg>A.A. Diversity in Global Studies, Pinecrest Community College</li>
  </ul>
  <div class="plain bar-title">Bar Admissions</div>
  <div class="plain">? Washington State</div>
  <div class="plain">(insert hyperlink) (insert hyperlink)</div>
</section>

<section class="collab-band abs" aria-label="Collaborative process"></section>
<h2 class="collab-title abs">COLLABORATIVE PROCESS</h2>
<p class="collab-lead abs">As you can see, there are plenty of reasons to consider Collaborative practice. It will help you to peacefully resolve conflicts and move through the legal process as efficiently and cost-effectively as possible.</p>
<div class="collab-cta abs"><b>Want to save money on court fees?</b> Consider the collaborative approach</div>
<div class="video abs"></div>
<div class="video-scene abs" role="img" aria-label="Animated explainer video scene of a legal office with a presenter"></div>
<div class="play abs"><svg width="64" height="42" viewBox="0 0 64 42"><path d="M25 10l16 11-16 11z" fill="#fff"/></svg></div>
<div class="controls abs"><svg width="10" height="10" viewBox="0 0 10 10"><path d="M1 0l8 5-8 5z" fill="#333"/></svg><span>0:00 / 0:00</span><span class="track"></span></div>

<footer class="site-footer abs"></footer>
<div class="brand footer-brand abs"><span class="brand-mark"></span><span class="brand-name">Vellmore Family Law</span></div>
<div class="contact-line abs" style="top:2425px">
  <span class="icon"><svg width="18" height="18" viewBox="0 0 24 24"><path d="M6 2l4 4-2 3a12 12 0 007 7l3-2 4 4-3 4C11 22 2 13 2 5z" fill="none" stroke="#fff" stroke-width="1.6"/></svg></span>
  <div><div class="label">CALL US AT:</div><div class="value">+ 123 456 7890</div></div>
</div>
<div class="contact-line abs" style="top:2499px">
  <span class="icon"><svg width="18" height="14" viewBox="0 0 18 14"><rect x="1" y="1" width="16" height="12" fill="none" stroke="#fff" stroke-width="1.4"/><path d="M1 1l8 7 8-7" fill="none" stroke="#fff" stroke-width="1.4"/></svg></span>
  <div><div class="label">MAIL US AT:</div><div class="value">info@vellmorefamily.com</div></div>
</div>

<form class="contact-panel abs" aria-label="Contact form">
  <h2>CONTACT US</h2>
  <div class="field" style="left:35px;top:105px;width:240px;height:47px">First Name</div>
  <div class="field" style="left:283px;top:105px;width:243px;height:47px">Last Name</div>
  <div class="field" style="left:35px;top:160px;width:240px;height:47px">Email</div>
  <div class="field" style="left:283px;top:160px;width:243px;height:47px">Phone</div>
  <div class="field msg" style="left:35px;top:214px;width:491px;height:74px">Message</div>
  <div class="submit">SUBMIT</div>
</form>

<div class="legal abs">Copyrights @ 2021 Vellmore Family Law. All Rights Reserved.</div>
</body>
</html>
```